Automotive Accessories Business Card

Design a business template that match our new logo design and our industry.

https://www.qelmotorgear.com/

Target Market(s)

Aftermarket auto parts and accessories

Industry/Entity Type

automotive

Contact Information for Business Card

company logo

Font styles to use
Serif
Sans Serif

Colors
EB3D1F
EC4F4E
F09395
F8D3D4
FCEDEE

```html
<!DOCTYPE html>
<html lang="en">
<head>
<meta charset="utf-8">
<title>QEL Motor Gear – Business Card</title>
<link href="https://fonts.googleapis.com/css2?family=Poppins:wght@400;500;600&display=swap" rel="stylesheet">
<style>
  :root {
    --bg: #0e0e0f;
    --card: #2a2a2c;
    --card-back: #262628;
    --red: #eb3d1f;
    --white: #ffffff;
    --muted: #d9d9dc;
    --rule: #56565a;
    --emboss: #3a3a3d;
  }
  * { box-sizing: border-box; margin: 0; padding: 0; }
  html, body {
    width: 1200px; height: 820px; overflow: hidden;
    background: var(--bg);
    font-family: "Poppins", sans-serif;
  }
  .stage {
    position: relative; width: 1200px; height: 820px;
    display: flex; align-items: center; justify-content: center; gap: 40px;
  }
  .card {
    position: relative; width: 540px; height: 309px;
    background: var(--card);
    box-shadow: 0 3px 0 var(--red), -3px 0 0 var(--red), 0 18px 40px rgba(0,0,0,.6);
  }
  .card--back { background: var(--card-back); box-shadow: 0 5px 0 var(--red), 0 18px 40px rgba(0,0,0,.6); }

  .brand {
    position: absolute; top: 62px; right: 88px;
    display: flex; align-items: center; gap: 10px;
  }
  .brand__mark { width: 18px; height: 18px; background: var(--red); }
  .brand__name {
    font-size: 26px; font-weight: 600; color: var(--white);
    letter-spacing: 1px; line-height: 1;
  }
  .brand-rule {
    position: absolute; top: 150px; left: 250px; right: 40px;
    height: 1px; background: var(--rule);
  }
  .person { position: absolute; left: 40px; top: 172px; }
  .person__name {
    font-size: 19px; font-weight: 600; color: var(--red);
    letter-spacing: .5px; text-transform: uppercase; line-height: 1.15;
  }
  .person__title { font-size: 15px; color: var(--white); line-height: 1.2; }
  .person-rule {
    position: absolute; left: 40px; top: 226px; width: 200px;
    height: 1px; background: var(--rule);
  }
  .contacts { position: absolute; left: 40px; top: 236px; list-style: none; }
  .contacts li {
    display: flex; align-items: center; gap: 8px;
    font-size: 14px; color: var(--white); line-height: 20px;
  }
  .contacts svg { width: 12px; height: 12px; flex: none; }
  .address {
    position: absolute; right: 40px; top: 164px;
    text-align: right; font-size: 14px; color: var(--white); line-height: 1.3;
  }

  .back-brand {
    position: absolute; inset: 0;
    display: flex; align-items: center; justify-content: center; gap: 14px;
  }
  .back-brand__mark { width: 26px; height: 26px; background: var(--emboss); }
  .back-brand__name {
    font-size: 40px; font-weight: 600; color: var(--emboss); letter-spacing: 1px;
  }
</style>
</head>
<body>
<main class="stage">
  <section class="card card--front">
    <div class="brand">
      <span class="brand__mark"></span>
      <span class="brand__name">QEL MOTOR GEAR</span>
    </div>
    <div class="brand-rule"></div>

    <div class="person">
      <p class="person__name">Marcus Delane</p>
      <p class="person__title">Managing Director</p>
    </div>
    <div class="person-rule"></div>

    <ul class="contacts">
      <li>
        <svg viewBox="0 0 24 24"><path fill="var(--red)" d="M6.6 10.8a15 15 0 0 0 6.6 6.6l2.2-2.2a1 1 0 0 1 1-.25 11.4 11.4 0 0 0 3.6.57 1 1 0 0 1 1 1V20a1 1 0 0 1-1 1A17 17 0 0 1 3 4a1 1 0 0 1 1-1h3.5a1 1 0 0 1 1 1c0 1.25.2 2.45.57 3.57a1 1 0 0 1-.25 1z"/></svg>
        044-987 210 345
      </li>
      <li>
        <svg viewBox="0 0 24 24"><rect x="2" y="5" width="20" height="14" fill="var(--red)"/><path d="M2 5l10 8 10-8" fill="none" stroke="var(--card)" stroke-width="2"/></svg>
        info@qelmotorgear.com
      </li>
      <li>
        <svg viewBox="0 0 24 24" fill="none" stroke="var(--red)" stroke-width="2"><circle cx="12" cy="12" r="10"/><path d="M2 12h20M12 2c3 3 3 17 0 20M12 2c-3 3-3 17 0 20"/></svg>
        www.qelmotorgear.com
      </li>
    </ul>

    <address class="address" style="font-style:normal">
      88, Harlow Ring Road<br>45090, Eastmere
    </address>
  </section>

  <section class="card card--back">
    <div class="back-brand">
      <span class="back-brand__mark"></span>
      <span class="back-brand__name">QEL MOTOR GEAR</span>
    </div>
  </section>
</main>
</body>
</html>
```